We want to design total new business card and logo for Kestrel Building Services Ltd

Our company name Kestrel Building Services Ltd. Design new logo and business card , need hi-end luxury style art for architecture and construction industry. The card should simple but stylish. Our business focus on CONNECT tradesman to construction company, help marketing construction company tender oversea projects, managing franchise in construction sector, delivery amazing services to our client, so Logo should show the CONNECTION IDEA, CONNECTING PEOPLE, LUXURY. Visit our website for more information: kestrelgroup.example.nz

Target Market(s)

Directors or managers

Industry/Entity Type

Construction Company

Contact Information for Business Card

Name, Title, Mobile, Email, Website

Font styles to use
Serif

Colors

Designer to choose colors to be used in the design.

Requirements
Must have
• Simple and luxury, connection icon
Nice to have
• Special materials, plastic card, look through,...
• Look new ideas.

```html
<!DOCTYPE html>
<html lang="en">
<head>
<meta charset="utf-8">
<title>Kestrel Building Services – Business Card</title>
<link rel="stylesheet" href="https://fonts.googleapis.com/css2?family=Open+Sans:wght@400;600;700&display=swap">
<style>
  :root {
    --teal: #06a7c6;
    --teal-light: #5cc8dc;
    --white: #ffffff;
    --ink: #3a3a3a;
    --rule: #9a9a9a;
    --backdrop: #e6e6e6;
  }
  html, body {
    margin: 0;
    width: 1200px;
    height: 802px;
    overflow: hidden;
    background: var(--backdrop);
    font-family: "Open Sans", Arial, sans-serif;
  }
  .card {
    position: absolute;
    top: 274px;
    width: 442px;
    height: 264px;
    box-shadow: 0 3px 8px rgba(0,0,0,.35);
    overflow: hidden;
  }
  .card--front { left: 136px; background: var(--teal); color: var(--white); }
  .card--back { left: 624px; background: var(--white); }

  .roof-decoration {
    position: absolute;
    left: 0; top: 0;
    width: 260px; height: 264px;
  }

  .contact {
    position: absolute;
    right: 22px;
    top: 58px;
    text-align: right;
    font-size: 13px;
    line-height: 16px;
  }
  .contact__name { font-weight: 600; font-size: 16px; line-height: 18px; letter-spacing: .2px; }
  .contact__title { margin-bottom: 12px; }
  .contact__line { display: flex; justify-content: flex-end; align-items: center; gap: 2px; }
  .contact__line svg { width: 10px; height: 10px; fill: var(--white); flex: none; }
  .contact__company { margin-top: 16px; font-weight: 700; padding-right: 2px; }
  .contact__address { padding-right: 2px; }

  .brand {
    position: absolute;
    left: 0; right: 0;
    top: 132px;
    text-align: center;
  }
  .brand__mark {
    width: 18px; height: 18px;
    border-radius: 50%;
    background: var(--teal);
    margin: 0 auto 12px;
  }
  .brand__name {
    color: var(--teal);
    font-weight: 600;
    font-size: 18px;
    line-height: 22px;
  }
  .brand__tagline {
    color: var(--ink);
    font-size: 12px;
    margin-top: 4px;
  }

  .social {
    position: absolute;
    left: 99px; right: 102px;
    top: 220px;
    display: flex;
    align-items: center;
    gap: 4px;
  }
  .social__rule { flex: 1; height: 1px; background: var(--rule); }
  .social__rule:first-child { margin-right: 4px; }
  .social__rule:last-child { margin-left: 4px; }
  .social__square { width: 18px; height: 18px; background: var(--teal); }
</style>
</head>
<body>
  <section class="card card--front">
    <svg class="roof-decoration" role="img" aria-label="Large white roof outline decoration" viewBox="0 0 260 264">
      <defs>
        <linearGradient id="roofFade" x1="0" y1="1" x2="1" y2="0">
          <stop offset="0" stop-color="#ffffff" stop-opacity=".45"/>
          <stop offset="1" stop-color="#ffffff" stop-opacity="0"/>
        </linearGradient>
      </defs>
      <rect width="260" height="264" fill="url(#roofFade)"/>
    </svg>

    <div class="contact">
      <div class="contact__name">MARCUS HALE</div>
      <div class="contact__title">Managing Director</div>
      <div class="contact__line">0800 555 014
        <svg viewBox="0 0 10 10"><path d="M1 4c0-2 8-2 8 0v1H7V4H3v1H1z M2.5 5.5h5L9 9H1z"/></svg>
      </div>
      <div class="contact__line">021 555 0192
        <svg viewBox="0 0 10 10"><path d="M1 4c0-2 8-2 8 0v1H7V4H3v1H1z M2.5 5.5h5L9 9H1z"/></svg>
      </div>
      <div class="contact__line">info@kestrelgroup.example.nz
        <svg viewBox="0 0 10 10"><path d="M0 2h10v6H0z" /><path d="M0 2l5 3.5L10 2" stroke="#06a7c6" stroke-width="1" fill="none"/></svg>
      </div>
      <div class="contact__line">www.kestrelgroup.example.nz
        <svg viewBox="0 0 10 10"><circle cx="5" cy="5" r="4.5"/><path d="M.5 5h9M5 .5c-2 2.5-2 6.5 0 9M5 .5c2 2.5 2 6.5 0 9" stroke="#06a7c6" stroke-width=".8" fill="none"/></svg>
      </div>
      <div class="contact__company">KESTREL BUILDING SERVICES LTD</div>
      <div class="contact__address">18 Ridgeway Road, Westmere</div>
      <div class="contact__address">Auckland 1022, Newzealand</div>
    </div>
  </section>

  <section class="card card--back">
    <div class="brand">
      <div class="brand__mark"></div>
      <div class="brand__name">KESTREL BUILDING SERVICES</div>
      <div class="brand__tagline">AMAZING SERVICES AFFORDABLE PRICE</div>
    </div>
    <div class="social">
      <span class="social__rule"></span>
      <span class="social__square"></span>
      <span class="social__square"></span>
      <span class="social__square"></span>
      <span class="social__square"></span>
      <span class="social__rule"></span>
    </div>
  </section>
</body>
</html>
```